Stylish Business Cards Wanted

- DOUBLE SIDED Design Required -

High end, edgy cards for a corporate and personal stylist. Must include logo,
Name: Belinda Harwick
Title: Director and Stylist
telephone : +61 8 7142 5809
email: belinda@theloombriefing.example
website: theloombriefing.example
Tag: Corporate Workwear & Uniform Specialist | Personal Stylist
Would like nice icons for telephone, email, website

Target Market(s)

Businesses wanting stylish uniforms, people wanting stylish wardrobes

Industry/Entity Type

Corporate Workwear Stylist

Contact Information for Business Card

I would like black, white and gold foiling incorporated in the design - possibly a touch of the other colours on my branding guide attached Name: Belinda Harwick Title: Director and Stylist telephone : +61 8 7142 5809 email: belinda@theloombriefing.example website: theloombriefing.example Tag: Corporate Workwear & Uniform Specialist | Personal Stylist Would like nice icons for telephone, email, website

Font styles to use
Other font styles liked:
• Raleway

Colors

Designer to choose colors to be used in the design.

Requirements
Must have
• Gold foil accents

```html
<!DOCTYPE html>
<html lang="en">
<head>
<meta charset="utf-8">
<title>The Loom Briefing – Business Cards</title>
<link rel="stylesheet" href="https://fonts.googleapis.com/css2?family=Raleway:wght@500;600;700;800&family=Montserrat:wght@500;600&display=swap">
<style>
  :root {
    --gold: #e8bf5a;
    --gold-deep: #d9ab3e;
    --ink: #0c0c0c;
    --paper: #ffffff;
    --stage: #dcdcdc;
    --muted: #333333;
  }
  * { box-sizing: border-box; margin: 0; padding: 0; }
  html, body { width: 1200px; height: 900px; overflow: hidden; }
  body {
    background: var(--stage);
    font-family: "Raleway", Arial, sans-serif;
    position: relative;
  }
  .card {
    position: absolute;
    width: 640px;
    height: 366px;
    overflow: hidden;
    box-shadow: 0 6px 14px rgba(0,0,0,0.22);
  }

  /* Front */
  .card-front {
    left: 200px; top: 60px;
    background: var(--ink);
    display: flex;
    flex-direction: column;
    justify-content: center;
    padding-left: 56px;
  }
  .front-wordmark {
    color: var(--gold);
    font-weight: 800;
    text-transform: uppercase;
    line-height: 0.95;
  }
  .front-wordmark .line-small { display: block; font-size: 40px; letter-spacing: 14px; }
  .front-wordmark .line-large { display: block; font-size: 96px; letter-spacing: 2px; }

  /* Back */
  .card-back {
    left: 360px; top: 470px;
    background: var(--paper);
  }
  .brand-block {
    position: absolute;
    left: 40px; top: 70px;
    width: 230px;
    text-align: center;
  }
  .brand-name {
    color: var(--ink);
    font-weight: 800;
    text-transform: uppercase;
    line-height: 1;
  }
  .brand-name .line-small { display: block; font-size: 16px; letter-spacing: 8px; }
  .brand-name .line-large { display: block; font-size: 40px; letter-spacing: 1px; margin-top: 4px; }
  .brand-tagline {
    margin-top: 22px;
    font-family: "Montserrat", Arial, sans-serif;
    font-weight: 500;
    font-size: 12.5px;
    line-height: 1.35;
    letter-spacing: 0.6px;
    color: var(--ink);
    text-transform: uppercase;
  }
  .divider {
    position: absolute;
    left: 296px; top: 44px;
    width: 2px; height: 236px;
    background: var(--gold);
  }
  .person {
    position: absolute;
    left: 330px; top: 62px;
  }
  .person-name {
    color: var(--gold);
    font-weight: 700;
    font-size: 25px;
    letter-spacing: 0.3px;
  }
  .person-title {
    color: var(--muted);
    font-weight: 500;
    font-size: 13px;
    margin-top: 2px;
  }
  .contact-list {
    position: absolute;
    left: 330px; top: 150px;
    list-style: none;
  }
  .contact-item {
    display: flex;
    align-items: center;
    gap: 14px;
    height: 30px;
    font-family: Arial, Helvetica, sans-serif;
    font-size: 14.5px;
    color: var(--ink);
  }
  .contact-icon { width: 18px; height: 18px; flex: none; }
  .base-rule {
    position: absolute;
    left: 0; right: 0; top: 300px;
    height: 3px;
    background: var(--gold);
  }
  .base-band {
    position: absolute;
    left: 0; right: 0; top: 318px; bottom: 0;
    background: var(--ink);
  }
</style>
</head>
<body>

  <section class="card card-front" aria-label="Business card front">
    <div class="front-wordmark">
      <span class="line-small">The</span>
      <span class="line-large">Loom</span>
      <span class="line-large">Briefing</span>
    </div>
  </section>

  <section class="card card-back" aria-label="Business card back">
    <div class="brand-block">
      <div class="brand-name">
        <span class="line-small">The</span>
        <span class="line-large">Loom Briefing</span>
      </div>
      <p class="brand-tagline">Corporate Workwear<br>Uniform Specialist<br>Personal Stylist</p>
    </div>

    <div class="divider"></div>

    <div class="person">
      <h1 class="person-name">Belinda Harwick</h1>
      <p class="person-title">Director and Stylist</p>
    </div>

    <ul class="contact-list">
      <li class="contact-item">
        <svg class="contact-icon" viewBox="0 0 24 24" aria-hidden="true">
          <path fill="var(--gold)" d="M6.6 10.8a15 15 0 0 0 6.6 6.6l2.2-2.2a1 1 0 0 1 1-.25 11.4 11.4 0 0 0 3.6.57 1 1 0 0 1 1 1V20a1 1 0 0 1-1 1A17 17 0 0 1 3 4a1 1 0 0 1 1-1h3.5a1 1 0 0 1 1 1c0 1.25.2 2.45.57 3.57a1 1 0 0 1-.25 1z"/>
        </svg>
        <span>+61 8 7142 5809</span>
      </li>
      <li class="contact-item">
        <svg class="contact-icon" viewBox="0 0 24 24" aria-hidden="true">
          <rect x="2" y="5" width="20" height="14" rx="1.5" fill="var(--gold)"/>
          <path d="M3 6.5l9 6.5 9-6.5" fill="none" stroke="var(--paper)" stroke-width="1.6"/>
        </svg>
        <span>belinda@theloombriefing.example</span>
      </li>
      <li class="contact-item">
        <svg class="contact-icon" viewBox="0 0 24 24" aria-hidden="true">
          <circle cx="12" cy="12" r="10" fill="var(--gold)"/>
          <g fill="none" stroke="var(--paper)" stroke-width="1.3">
            <ellipse cx="12" cy="12" rx="4" ry="10"/>
            <path d="M2 12h20M4 7h16M4 17h16"/>
          </g>
        </svg>
        <span>theloombriefing.example</span>
      </li>
    </ul>

    <div class="base-rule"></div>
    <div class="base-band"></div>
  </section>

</body>
</html>
```